Brookvale Building Company - advertisement poster

I am looking to print some canvas signs to advertise my general contracting company, Brookvale Building Company. The sign will measure 6' long x 3' high so the size should match that ratio. I already have a logo icon, which is the Letter 'B' and some trees that I would like to incorporate, see attached. I would also like the to have the following information listed:
1) phone number: 831-555-0172
2) email: brookvalebuildingcompany@mailnest.example
3) website: brookvalebuildingcompany.example
4) Lic#4826130
5) I want to use this text: "BUILD WITH THE B-CREW!"

The ad should be relatively simple and clean. Black and Green are my company colors. I am open to creative ideas!

Target Market(s)

People looking to renovate their homes

Industry/Entity Type

Construction

Colors
59FF00
82FF00
B8FF75
E3FFCB
F4FFEA

Requirements
Must have
• Must have my company logo
Should not have
• No photos or complex graphics

```html
<!DOCTYPE html>
<html lang="en">
<head>
<meta charset="utf-8">
<title>Brookvale Building Company – Build with the B-Crew</title>
<link rel="stylesheet" href="https://fonts.googleapis.com/css2?family=Orbitron:wght@500;700;800&display=swap">
<style>
  :root {
    --page: #ffffff;
    --band-top: #373737;
    --band-mid: #202122;
    --band-low: #141516;
    --band-base: #070707;
    --ink: #ffffff;
    --green: #71b546;
  }
  * { box-sizing: border-box; margin: 0; padding: 0; }
  html, body {
    width: 1200px; height: 741px; overflow: hidden;
    background: var(--page);
    font-family: "Orbitron", sans-serif;
  }
  .poster {
    position: absolute; left: 78px; top: 94px;
    width: 1043px; height: 522px;
    background: var(--band-top);
    overflow: hidden;
    color: var(--ink);
  }
  .poster-backdrop { position: absolute; inset: 0; }
  .headline-top {
    position: absolute; left: 40px; right: 40px; top: 32px;
    display: flex; justify-content: space-between;
    font-weight: 700; font-size: 48px; line-height: 1;
  }
  .headline-top .word { display: flex; gap: 0; }
  .headline-top .word span { width: 66px; text-align: center; }
  .center-mark {
    position: absolute; left: 0; right: 0; top: 118px;
    display: flex; flex-direction: column; align-items: center; gap: 14px;
  }
  .center-mark .mark-square { width: 74px; height: 74px; background: var(--green); }
  .center-mark .mark-name {
    font-weight: 700; font-size: 24px; letter-spacing: 2px;
    text-align: center; line-height: 1.25; text-transform: uppercase;
  }
  .headline-crew {
    position: absolute; left: 0; right: 0; top: 280px;
    text-align: center; font-weight: 800; font-size: 60px; line-height: 1;
  }
  .contacts {
    position: absolute; left: 38px; top: 380px;
    list-style: none; display: flex; flex-direction: column; gap: 16px;
  }
  .contacts li { display: flex; align-items: center; gap: 12px; font-weight: 500; line-height: 1; }
  .contacts .icon { width: 24px; height: 24px; flex: none; }
  .contacts .phone { font-size: 26px; letter-spacing: 3px; }
  .contacts .email, .contacts .web { font-size: 18.5px; letter-spacing: 1px; }
  .brand-block {
    position: absolute; left: 768px; top: 316px; width: 250px;
    display: flex; flex-direction: column; align-items: center;
  }
  .brand-block .mark-square { width: 84px; height: 84px; background: var(--green); }
  .brand-block .mark-name {
    margin-top: 12px; font-weight: 700; font-size: 17px; letter-spacing: 1.5px;
    text-align: center; line-height: 1.3; text-transform: uppercase;
  }
  .license { margin-top: 12px; font-size: 15px; font-weight: 500; letter-spacing: 1px; }
  .license .label { color: var(--green); }
</style>
</head>
<body>
<main class="poster">
  <svg class="poster-backdrop" viewBox="0 0 1043 522" preserveAspectRatio="none" aria-hidden="true">
    <polygon points="0,102 522,337 1043,102 1043,522 0,522" fill="var(--band-mid)"/>
    <polygon points="0,249 522,403 1043,249 1043,522 0,522" fill="var(--band-low)"/>
    <polygon points="0,383 522,440 1043,383 1043,522 0,522" fill="var(--band-base)"/>
  </svg>

  <h1 class="headline-top" aria-label="Build with the">
    <span class="word"><span>B</span><span>U</span><span>I</span><span>L</span><span>D</span></span>
    <span class="word"><span>W</span><span>I</span><span>T</span><span>H</span></span>
    <span class="word"><span>T</span><span>H</span><span>E</span></span>
  </h1>

  <div class="center-mark">
    <div class="mark-square"></div>
    <p class="mark-name">Brookvale Building Company</p>
  </div>

  <p class="headline-crew">B-CREW!</p>

  <ul class="contacts">
    <li class="phone">
      <svg class="icon" viewBox="0 0 24 24" fill="none" stroke="var(--green)" stroke-width="2.2"><circle cx="12" cy="12" r="10"/><path d="M8 7.5l2 .2.8 2.3-1.2 1.2a7 7 0 0 0 3.2 3.2l1.2-1.2 2.3.8.2 2a1.5 1.5 0 0 1-1.7 1.4A9 9 0 0 1 6.6 9.2 1.5 1.5 0 0 1 8 7.5z"/></svg>
      831-555-0172
    </li>
    <li class="email">
      <svg class="icon" viewBox="0 0 24 24" fill="none" stroke="var(--green)" stroke-width="2.2"><rect x="2" y="5" width="20" height="15" rx="2"/><path d="M3 7l9 6 9-6"/></svg>
      brookvalebuildingcompany@mailnest.example
    </li>
    <li class="web">
      <svg class="icon" viewBox="0 0 24 24" fill="none" stroke="var(--green)" stroke-width="2.2"><circle cx="12" cy="12" r="10"/><ellipse cx="12" cy="12" rx="4.5" ry="10"/><path d="M2 12h20M12 2v20"/></svg>
      brookvalebuildingcompany.example
    </li>
  </ul>

  <div class="brand-block">
    <div class="mark-square"></div>
    <p class="mark-name">Brookvale<br>Building Company</p>
    <p class="license"><span class="label">Lic#</span>4826130</p>
  </div>
</main>
</body>
</html>
```